Company web site

Looking for a full responsive(mobile friendly) wordpress implementation

Some material is in the website -- brelvanto.wordpress.com

But looking for a template more consistent with the logo design, and more future looking.

Target Market(s)

Enterprise Clients

Industry/Entity Type

It Company

Font styles to use
Sans Serif

Colors
33a6d7
0255a3
0455a3
cfdeed
85abd2
3176b5

Requirements
Must have
• about, contact information, partner page, success stories, customer testimonials. links to social presence.
• pricing information

```html
<!DOCTYPE html>
<html lang="en">
<head>
<meta charset="utf-8">
<title>Brelvanto — Home</title>
<link rel="stylesheet" href="https://fonts.googleapis.com/css2?family=Open+Sans:ital,wght@0,400;0,600;0,700;1,400&family=Roboto:wght@300;400;500;700&display=swap">
<style>
:root{
  --sky:#33a6d7;
  --navy:#0255a3;
  --navy-2:#0455a3;
  --mist:#cfdeed;
  --steel:#85abd2;
  --mid:#3176b5;
  --ink:#222;
  --text:#555;
  --muted:#888;
  --grey-band:#ececec;
  --white:#fff;
  --orange:#e8862a;
}
*{box-sizing:border-box;margin:0;padding:0}
html,body{width:1200px;height:3550px;overflow:hidden;background:var(--white)}
body{font-family:"Open Sans",Arial,sans-serif;color:var(--text);position:relative}
.abs{position:absolute}
h1,h2,h3,h4{font-family:"Roboto",Arial,sans-serif;font-weight:400;color:var(--ink)}

/* header */
.site-header{position:absolute;left:0;top:0;width:1200px;height:114px;background:var(--white)}
.brand{left:100px;top:26px;display:flex;align-items:center;gap:12px}
.brand-dot{width:46px;height:46px;border-radius:50%;background:var(--sky)}
.brand-name{font-family:"Roboto",sans-serif;font-weight:700;font-size:30px;color:var(--navy)}
.top-contact{right:100px;top:20px;display:flex;gap:38px;font-size:15px;color:var(--text)}
.top-contact span{display:flex;align-items:center;gap:10px}
.top-contact i{width:26px;height:26px;border-radius:50%;background:var(--sky);display:inline-flex;align-items:center;justify-content:center}
.main-nav{right:100px;top:68px;display:flex;gap:30px;font-family:"Roboto",sans-serif;font-size:13.5px;font-weight:500;text-transform:uppercase;color:#444}
.main-nav a{color:inherit;text-decoration:none;padding-bottom:14px}
.main-nav a.active{color:var(--sky);border-bottom:3px solid var(--sky)}

/* hero */
.hero{left:0;top:114px;width:1200px;height:566px;background:linear-gradient(100deg,#1a1d22 0%,#2b3038 45%,#4a5563 70%,#2a2f36 100%)}
.hero-visual{left:560px;top:0;width:640px;height:566px;background:radial-gradient(ellipse at 55% 40%,rgba(220,235,250,.55),rgba(51,166,215,.25) 35%,rgba(20,24,30,0) 70%)}
.hero-title{left:100px;font-family:"Roboto",sans-serif;font-weight:700;font-size:44px;color:var(--white);letter-spacing:1px}
.hero-text{left:100px;width:420px;font-size:15px;line-height:1.55;color:#dde3ea}
.btn-outline{left:100px;border:1px solid #cfd6de;color:var(--white);font-size:12.5px;font-weight:600;padding:11px 16px;text-transform:uppercase;display:flex;gap:8px;align-items:center}
.dots{left:568px;display:flex;gap:6px}
.dots i{width:13px;height:13px;border-radius:50%;border:2px solid var(--white)}
.dots i.on{background:#e9b84a;border-color:#e9b84a}

/* welcome */
.welcome-title{left:109px;top:790px;font-size:38px;font-weight:500}
.welcome-copy{left:109px;top:845px;width:530px;font-size:12.5px;line-height:1.75}
.welcome-copy .lead{font-size:17px;color:#333;margin:14px 0 10px}
.btn-pill{background:var(--mid);color:var(--white);font-size:11.5px;font-weight:700;text-transform:uppercase;border-radius:20px;padding:9px 18px;display:inline-flex;gap:8px;align-items:center}
.monitor{left:696px;top:762px;width:393px;height:279px}

/* ensures */
.ensures{left:0;top:1160px;width:1200px;height:540px;background:linear-gradient(180deg,#2f9fdc 0%,#2a8fd6 100%);overflow:hidden}
.ensures h2{position:absolute;left:0;width:1200px;top:56px;text-align:center;color:var(--white);font-size:36px;font-weight:400}
.ensures .sub{position:absolute;left:0;width:1200px;top:110px;text-align:center;color:var(--white);font-size:16px}
.step{position:absolute;color:var(--white);font-size:11px;line-height:1.4;width:230px}
.step b{display:block;font-family:"Roboto",sans-serif;font-weight:400;font-size:17px;margin-bottom:4px}
.step.left{text-align:right}
.hub-name{position:absolute;left:0;width:1200px;top:1598px;z-index:2;text-align:center;font-family:"Roboto",sans-serif;font-weight:700;font-size:34px;color:var(--sky)}

/* platform */
.tablet{left:99px;top:1822px;width:471px;height:438px}
.platform-title{left:644px;top:1830px;font-size:29px;font-weight:500;text-transform:uppercase}
.platform-copy{left:644px;top:1880px;width:460px;font-size:13.5px;line-height:1.6;color:#333}
.platform-copy ul{list-style:none;margin-top:12px}
.platform-copy li{font-size:11.5px;color:#444;margin-bottom:10px;display:flex;gap:12px;align-items:center}
.platform-copy li::before{content:"";width:0;height:0;border-left:6px solid #555;border-top:4px solid transparent;border-bottom:4px solid transparent}

/* testimonials */
.testimonials{left:0;top:2260px;width:1200px;height:403px;background:var(--grey-band)}
.section-title{position:absolute;left:0;width:1200px;text-align:center;font-size:30px;font-weight:400;color:#333;text-transform:uppercase}
.rule{position:absolute;left:570px;width:60px;height:2px;background:var(--sky)}
.quote{position:absolute;width:330px}
.avatar{position:absolute;width:118px;height:118px;border-radius:50%;border:4px solid var(--white);background:radial-gradient(circle at 50% 40%,#d9c3ae,#8d7a6a)}
.quote p{font-style:italic;font-size:12px;line-height:1.6;color:#555;white-space:normal}
.quote .who{font-family:"Roboto",sans-serif;font-size:12.5px;font-weight:500;color:#333;margin:14px 0 6px;text-transform:uppercase}
.stars{color:var(--orange);font-size:14px;letter-spacing:1px}
.stars em{color:#444;font-style:normal}

/* stories */
.story{position:absolute;width:313px}
.story .photo{height:166px}
.story h4{font-family:"Open Sans",sans-serif;font-size:15px;color:#444;margin:34px 0 12px}
.story .meta{display:flex;gap:26px;font-size:11.5px;color:#666;font-style:italic}
.story p{font-size:11.5px;line-height:1.65;color:#666;margin-top:16px}

/* footer */
.site-footer{left:0;top:3207px;width:1200px;height:308px;background:linear-gradient(180deg,#1b63b6,#1859a8)}
.fcol{position:absolute;top:58px;color:var(--white);font-size:12.5px;line-height:1.6}
.fcol h4{color:var(--white);font-size:17px;font-weight:400;text-transform:uppercase;margin-bottom:22px;letter-spacing:.5px}
.frow{display:flex;gap:16px;margin-bottom:14px}
.frow svg{flex:none;margin-top:2px}
.tweet{display:flex;gap:14px;margin-bottom:12px;font-size:11px;line-height:1.5}
.tweet .sq{flex:none;width:18px;height:18px;background:var(--white);border-radius:3px}
.field{width:240px;height:40px;background:var(--white);color:#999;font-size:11px;padding:12px;margin:18px 0 10px}
.subscribe{display:inline-block;background:var(--orange);color:var(--white);font-size:11.5px;font-weight:700;text-transform:uppercase;padding:11px 16px}
.socials{display:inline-flex;gap:8px;margin-left:18px;vertical-align:middle}
.socials i{width:24px;height:24px;border-radius:50%;background:var(--white)}
.quick a{display:block;color:var(--white);text-decoration:none;font-size:12px;line-height:1.65}
.bottom-bar{left:0;top:3515px;width:1200px;height:35px;background:#0f4a92;color:#c9d8ea;font-size:11px;text-align:center;line-height:35px}
</style>
</head>
<body>

<header class="site-header">
  <div class="abs brand"><span class="brand-dot"></span><span class="brand-name">Brelvanto</span></div>
  <div class="abs top-contact">
    <span><i><svg width="12" height="12" viewBox="0 0 24 24"><path fill="#fff" d="M6.6 10.8a15 15 0 006.6 6.6l2.2-2.2a1 1 0 011-.3 11 11 0 003.6.6 1 1 0 011 1V20a1 1 0 01-1 1A17 17 0 013 4a1 1 0 011-1h3.5a1 1 0 011 1c0 1.2.2 2.5.6 3.6a1 1 0 01-.3 1z"/></svg></i>+1 (555) 014-2290</span>
    <span><i><svg width="12" height="12" viewBox="0 0 24 24"><path fill="#fff" d="M3 5h18v14H3z"/><path fill="none" stroke="#33a6d7" stroke-width="2" d="M3 6l9 7 9-7"/></svg></i>info@brelvanto.com</span>
  </div>
  <nav class="abs main-nav">
    <a class="active">Home</a><a>About</a><a>Partners</a><a>Pricing</a><a>Success Stories</a><a>Testimonials</a><a>Contact Us</a>
  </nav>
</header>

<section class="abs hero">
  <div class="abs hero-visual" role="img" aria-label="Hand holding a tablet with a glowing cloud of connected device icons above it"></div>
  <h1 class="abs hero-title" style="top:170px">BRELVANTO</h1>
  <p class="abs hero-text" style="top:236px">Duis aute irure dolor in reprehenderit in voluptate velit esse cillum dolore eu fugiat nulla pariatur. Excepteur sint occaecat cupidatat non proident, sunt</p>
  <div class="abs btn-outline" style="top:316px">Read more <svg width="14" height="14" viewBox="0 0 24 24"><circle cx="12" cy="12" r="11" fill="#fff"/><path d="M10 7l5 5-5 5" stroke="#222" stroke-width="2.5" fill="none"/></svg></div>
  <div class="abs dots" style="top:498px"><i class="on"></i><i></i><i></i><i></i></div>
</section>

<section>
  <h2 class="abs welcome-title">WELCOME TO BRELVANTO</h2>
  <div class="abs welcome-copy">
    <p>Founded in 2016 by industry veterans, Brelvanto is geared to provide integrated solutions for the IoT industry. With a off-shore development center in Eastern Europe, Brelvanto is positioned to provide extensive development capabilities to our customers.</p>
    <p class="lead">Focus on your product. We manage the integrations.</p>
    <p>With Brelvanto you pick-and-choose the features your customers want, based on our modular architecture. And get all the tools you need to operate your IoT business.</p>
    <p style="margin-top:22px"><span class="btn-pill">Read more <svg width="13" height="13" viewBox="0 0 24 24"><circle cx="12" cy="12" r="11" fill="#fff"/><path d="M10 7l5 5-5 5" stroke="#3176b5" stroke-width="2.5" fill="none"/></svg></span></p>
  </div>
  <svg class="abs monitor" viewBox="0 0 393 279" role="img" aria-label="Desktop monitor showing a device tracking dashboard with a map">
    <rect x="0" y="0" width="393" height="238" rx="8" fill="#1d1f22"/>
    <rect x="10" y="10" width="373" height="218" fill="#e6edf3"/>
    <rect x="10" y="10" width="373" height="16" fill="#2f6fb5"/>
    <rect x="18" y="34" width="357" height="110" fill="#cdd9c8"/>
    <rect x="18" y="152" width="357" height="68" fill="#f7f9fb"/>
    <path d="M180 238h34l8 28h-50z" fill="#c9ccd0"/>
    <rect x="140" y="266" width="114" height="8" rx="3" fill="#d6d8db"/>
  </svg>
</section>

<section class="abs ensures">
  <h2>BRELVANTO ENSURES</h2>
  <p class="sub">end-to-end product lifecycle management.</p>
  <svg class="abs" style="left:0;top:0" width="1200" height="540" viewBox="0 0 1200 540">
    <g stroke="#fff" stroke-width="2.5" fill="none">
      <line x1="601" y1="540" x2="502" y2="244"/>
      <line x1="601" y1="540" x2="686" y2="244"/>
      <line x1="601" y1="540" x2="372" y2="331"/>
      <line x1="601" y1="540" x2="805" y2="331"/>
      <line x1="601" y1="540" x2="308" y2="450"/>
      <line x1="601" y1="540" x2="880" y2="450"/>
    </g>
    <path d="M405 540a196 196 0 01392 0z" fill="#fff"/>
    <g fill="#2f9fdc" stroke="#fff" stroke-width="3">
      <circle cx="502" cy="244" r="40"/><circle cx="686" cy="244" r="40"/>
      <circle cx="372" cy="331" r="40"/><circle cx="805" cy="331" r="40"/>
      <circle cx="308" cy="450" r="40"/><circle cx="880" cy="450" r="40"/>
    </g>
    <g fill="none" stroke="#fff" stroke-width="2.5" stroke-linecap="round" stroke-linejoin="round">
      <circle cx="497" cy="248" r="8"/><circle cx="497" cy="248" r="14" stroke-dasharray="5 4"/><circle cx="514" cy="234" r="5"/>
      <path d="M672 250v-8a14 14 0 0128 0v8"/><rect x="669" y="248" width="7" height="12" rx="2"/><rect x="696" y="248" width="7" height="12" rx="2"/>
      <path d="M358 326l12-12h16v16l-12 12z"/><circle cx="381" cy="319" r="2.5"/>
      <path d="M790 344v-26M790 344h30M794 338l8-9 6 5 10-12"/>
      <path d="M294 458h26a8 8 0 000-16 12 12 0 00-23-3 9 9 0 00-3 19z"/><circle cx="310" cy="454" r="4"/>
      <rect x="866" y="438" width="28" height="26" rx="2"/><path d="M866 446h28M872 434v6M888 434v6M872 452h4M880 452h4M888 452h4M872 458h4M880 458h4"/>
    </g>
  </svg>
  <div class="step left" style="left:218px;top:212px"><b>Manufacture</b>Secure manufacturing process.<br>Device traceability in ERP</div>
  <div class="step" style="left:738px;top:212px"><b>Support</b>In app chat, ticketing<br>system and call center integration.</div>
  <div class="step left" style="left:88px;top:298px"><b>Sell</b>End user tracking in CRM<br>Social identity for proactive marketing</div>
  <div class="step" style="left:858px;top:298px;width:260px"><b>Monetize</b>Recurrent user billing<br>Additional services and payment options.</div>
  <div class="step left" style="left:24px;top:418px"><b>Provision</b>Simplify consumer experience<br>during device activation</div>
  <div class="step" style="left:932px;top:418px"><b>Maintain</b>Device health check<br>Software and security updates</div>
</section>
<div class="hub-name">Brelvanto</div>

<section>
  <svg class="abs tablet" viewBox="0 0 471 438" role="img" aria-label="Tablet showing a platform architecture diagram of devices linked to cloud services">
    <rect x="0" y="0" width="471" height="438" rx="8" fill="#111"/>
    <rect x="16" y="18" width="439" height="420" fill="#f4f6f8"/>
    <rect x="80" y="80" width="320" height="300" fill="#e3e9ef"/>
  </svg>
  <h2 class="abs platform-title">The Brelvanto Platform</h2>
  <div class="abs platform-copy">
    <p>Connecting new products across clouds and enterprise solutions is now easier than ever.</p>
    <p style="margin-top:16px">Your license includes:</p>
    <ul>
      <li>A dedicated instance in the Brelvanto PaaS cloud (*)</li>
      <li>Orbix and Velo OS mobile SDK with white label mobile app</li>
      <li>App notifications</li>
      <li>Customizable web portal for users</li>
      <li>Brelvanto sample device code</li>
      <li>NOC - Network Operation Center</li>
      <li>Multi-level user management web application</li>
      <li>Security updates</li>
    </ul>
  </div>
</section>

<section class="abs testimonials">
  <h2 class="section-title" style="top:76px">Testimonials</h2>
  <div class="rule" style="top:128px"></div>
  <div class="avatar" role="img" aria-label="Client portrait" style="left:99px;top:188px"></div>
  <div class="quote" style="left:238px;top:188px">
    <p>“ Nemo enim ipsam voluptatem quia voluptas sit aspernatur aut odit aut fugit, sed quia consequuntur magni dolores eos qui ratione voluptatem sequi nesciunt.</p>
    <div class="who">Dana Holm - Brelvanto</div>
    <div class="stars">★★★★<em>★</em></div>
  </div>
  <div class="avatar" role="img" aria-label="Client portrait" style="left:636px;top:188px"></div>
  <div class="quote" style="left:776px;top:188px">
    <p>“ Nemo enim ipsam voluptatem quia voluptas sit aspernatur aut odit aut fugit, sed quia consequuntur magni dolores eos qui ratione voluptatem sequi nesciunt.</p>
    <div class="who">Dana Holm - Brelvanto</div>
    <div class="stars">★★★★<em>★</em></div>
  </div>
</section>

<section>
  <h2 class="section-title" style="top:2730px">Success Stories</h2>
  <article class="story" style="left:99px;top:2821px">
    <div class="photo" role="img" aria-label="Person in a dark control room facing large data screens" style="background:linear-gradient(135deg,#1e2a3a,#5d7590 60%,#25313f)"></div>
    <h4>Nemo enim ipsam voluptatem quia</h4>
    <div class="meta"><span>▦ March 25, 2017</span><span>◌ No comments</span></div>
    <p>Lorem ipsum dolor sit amet, consectetur adipiscing elit, sed do eiusmod tempor incididunt ut labore et dolore magna aliqua. Ut enim ad minim veniam,</p>
  </article>
  <article class="story" style="left:443px;top:2821px">
    <div class="photo" role="img" aria-label="Hands typing on a laptop keyboard" style="background:linear-gradient(135deg,#9aa3ad,#d9dde2 55%,#7e8690)"></div>
    <h4>Nemo enim ipsam voluptatem quia</h4>
    <div class="meta"><span>▦ March 25, 2017</span><span>◌ No comments</span></div>
    <p>Lorem ipsum dolor sit amet, consectetur adipiscing elit, sed do eiusmod tempor incididunt ut labore et dolore magna aliqua. Ut enim ad minim veniam,</p>
  </article>
  <article class="story" style="left:786px;top:2821px">
    <div class="photo" role="img" aria-label="Business team meeting around a laptop in a bright office" style="background:linear-gradient(135deg,#c4ccd4,#f0f2f4 50%,#5f6770)"></div>
    <h4>Nemo enim ipsam voluptatem quia</h4>
    <div class="meta"><span>▦ March 25, 2017</span><span>◌ No comments</span></div>
    <p>Lorem ipsum dolor sit amet, consectetur adipiscing elit, sed do eiusmod tempor incididunt ut labore et dolore magna aliqua. Ut enim ad minim veniam,</p>
  </article>
</section>

<footer class="abs site-footer">
  <div class="fcol" style="left:99px;width:260px">
    <h4>Contact Us</h4>
    <div class="frow"><svg width="14" height="18" viewBox="0 0 14 18"><path d="M7 0a7 7 0 00-7 7c0 5 7 11 7 11s7-6 7-11a7 7 0 00-7-7z" fill="#fff"/><circle cx="7" cy="7" r="2.5" fill="#1b63b6"/></svg><span>Brelvanto<br>418 Harlow Ave<br>Larkspur Bay, CA 94021</span></div>
    <div class="frow"><svg width="14" height="16" viewBox="0 0 24 24"><path fill="#fff" d="M6.6 10.8a15 15 0 006.6 6.6l2.2-2.2a1 1 0 011-.3 11 11 0 003.6.6 1 1 0 011 1V20a1 1 0 01-1 1A17 17 0 013 4a1 1 0 011-1h3.5a1 1 0 011 1c0 1.2.2 2.5.6 3.6a1 1 0 01-.3 1z"/></svg><span>Phone : +1 (555) 014-2290</span></div>
    <div class="frow"><svg width="16" height="14" viewBox="0 0 24 18"><rect x="1" y="1" width="22" height="16" fill="none" stroke="#fff" stroke-width="2"/><path d="M1 2l11 8 11-8" fill="none" stroke="#fff" stroke-width="2"/></svg><span>info@brelvanto.com</span></div>
  </div>
  <div class="fcol" style="left:383px;width:270px">
    <h4>Latest Tweet's</h4>
    <div class="tweet"><span class="sq"></span><span>@Brelvanto. Fusce suscit varius mi. Cum sociis natoque penatibus et<br>1 day ago</span></div>
    <div class="tweet"><span class="sq"></span><span>@Brelvanto. Fusce suscit varius mi. Cum sociis natoque penatibus et<br>1 day ago</span></div>
  </div>
  <div class="fcol" style="left:691px;width:290px">
    <h4>Join Our Newsletter</h4>
    <p style="font-size:11.5px;width:240px">Excepteur sint occaecat cupidatat non proident, sunt in culpa qui</p>
    <div class="field">Enter Name</div>
    <span class="subscribe">Subscribe</span><span class="socials"><i></i><i></i><i></i><i></i></span>
  </div>
  <div class="fcol quick" style="left:994px;width:140px">
    <h4>Quick Links</h4>
    <a>About</a><a>Partners</a><a>Pricing</a><a>Success Stories</a><a>News</a><a>Testimonials</a><a>Contact us</a>
  </div>
</footer>
<div class="abs bottom-bar">©2017 Brelvanto... All Rights Reserved.</div>

</body>
</html>
```